Brightmill Data Works

Our company is about IT hardwares and IT solutions. IT hardware such as PC, RAMS, storage and servers. IT solutions such as project management, BA. We are also selling new technology too.

Target Market(s)

Consumer, Small to Medium Business, Corporate

Requirements
Must have
• The business card must have the following:
• Name:
• Title:
• Contact Number:
• Email address:
• Website:
• Color: Must match the logo color upgrade

```html
<!DOCTYPE html>
<html lang="en">
<head>
<meta charset="utf-8">
<title>Brightmill Data Works — Business Card</title>
<link rel="stylesheet" href="https://fonts.googleapis.com/css2?family=Arimo:wght@400;700&display=swap">
<style>
  :root {
    --page-bg: #2a2a2a;
    --card-bg: #1b1b1b;
    --card-edge: #262626;
    --ink: #ffffff;
    --accent: #e0862a;
    --muted: #d9d9d9;
  }
  * { box-sizing: border-box; margin: 0; padding: 0; }
  html, body {
    width: 1200px;
    height: 1189px;
    overflow: hidden;
    background: var(--page-bg);
    font-family: "Arimo", Arial, sans-serif;
  }
  .sheet {
    width: 1200px;
    height: 1189px;
    display: flex;
    flex-direction: column;
    align-items: center;
    justify-content: center;
    gap: 44px;
  }
  .card {
    position: relative;
    width: 900px;
    height: 514px;
    background: var(--card-bg);
    border: 1px solid var(--card-edge);
    border-radius: 42px;
    overflow: hidden;
  }

  /* Front */
  .card--front {
    display: flex;
    align-items: center;
    justify-content: center;
  }
  .brand {
    display: flex;
    align-items: center;
    gap: 18px;
  }
  .brand__mark {
    width: 34px;
    height: 34px;
    background: var(--accent);
    border-radius: 4px;
    flex: none;
  }
  .brand__name {
    color: var(--ink);
    font-weight: 700;
    font-size: 50px;
    line-height: 1.05;
    letter-spacing: 0.5px;
  }

  /* Back */
  .card--back .brand {
    position: absolute;
    left: 90px;
    top: 170px;
    width: 370px;
  }
  .card--back .brand__name {
    font-size: 40px;
  }
  .divider {
    position: absolute;
    left: 492px;
    top: 120px;
    width: 2px;
    height: 150px;
    background: var(--accent);
  }
  .contact {
    position: absolute;
    left: 530px;
    top: 110px;
    color: var(--ink);
  }
  .contact__name {
    font-weight: 700;
    font-size: 22px;
    letter-spacing: 0.5px;
  }
  .contact__title {
    color: var(--accent);
    font-size: 20px;
    margin-bottom: 14px;
  }
  .contact__list {
    list-style: none;
    font-size: 19px;
    line-height: 1.45;
    color: var(--muted);
  }
  .contact__list li {
    display: flex;
    align-items: center;
    gap: 12px;
  }
  .contact__list svg {
    width: 16px;
    height: 16px;
    flex: none;
  }
  .address {
    position: absolute;
    left: 0;
    right: 0;
    bottom: 70px;
    text-align: center;
    color: var(--ink);
    font-size: 22px;
    letter-spacing: 0.3px;
  }
</style>
</head>
<body>
<main class="sheet">

  <section class="card card--front" aria-label="Card front">
    <div class="brand">
      <span class="brand__mark"></span>
      <span class="brand__name">Brightmill<br>Data Works</span>
    </div>
  </section>

  <section class="card card--back" aria-label="Card back">
    <div class="brand">
      <span class="brand__mark"></span>
      <span class="brand__name">Brightmill<br>Data Works</span>
    </div>

    <span class="divider"></span>

    <div class="contact">
      <p class="contact__name">DARREN OKAFOR</p>
      <p class="contact__title">Manager</p>
      <ul class="contact__list">
        <li>
          <svg viewBox="0 0 16 16" aria-hidden="true"><path fill="#e0862a" d="M3.6 1.2l2.3 2.5-1.3 1.8c.9 2 2.3 3.5 4.3 4.5l1.8-1.3 2.5 2.3-1.2 2.6C7.6 13.3 2.8 8.4 1 3.4z"/></svg>
          555-018-4420
        </li>
        <li>
          <svg viewBox="0 0 16 16" aria-hidden="true"><rect x="1" y="3.5" width="14" height="9" fill="#e0862a"/><path d="M1 3.5l7 5 7-5" fill="none" stroke="#1b1b1b" stroke-width="1.3"/></svg>
          hello@brightmilldata.com
        </li>
        <li>
          <svg viewBox="0 0 16 16" aria-hidden="true"><g fill="none" stroke="#e0862a" stroke-width="1.4"><circle cx="8" cy="8" r="6.5"/><ellipse cx="8" cy="8" rx="2.8" ry="6.5"/><path d="M1.5 8h13M2.6 4.5h10.8M2.6 11.5h10.8"/></g></svg>
          www.brightmilldata.com
        </li>
      </ul>
    </div>

    <p class="address">PO BOX 48 Harlow Lane, 7th street Eastbrook</p>
  </section>

</main>
</body>
</html>
```